Business card design needed

I would like a one sided black business card with the information provided above. Refer to my website www.brightvolleyracquets.com.au for an example of colors I have used for my site, would like to keep this consistent for my business cards also, I will upload my logo below.

I am a new small business that provides tennis customers with racquet re stringing, tennis strings and accessories.

Industry/Entity Type

Small Business

Contact Information for Business Card

Bright Volley Tennis

Owen Whitby
Managing Director

brightvolleyracquets@mailbox.example
www.brightvolleyracquets.com.au
0491 726 305

Racquet Restringing/Tennis Strings/Accessories

Requirements
Must have
• Must have my logo and card must be black

```html
<!DOCTYPE html>
<html lang="en">
<head>
<meta charset="utf-8">
<title>Bright Volley Tennis – Business Card</title>
<link rel="stylesheet" href="https://fonts.googleapis.com/css2?family=Open+Sans:wght@400;600;700&display=swap">
<style>
  :root {
    --backdrop: #e9e6e1;
    --card-black: #000000;
    --lime: #b5d334;
    --white: #ffffff;
    --divider: #6b6b6b;
  }
  html, body {
    margin: 0;
    width: 1200px;
    height: 750px;
    overflow: hidden;
    background: var(--backdrop);
    font-family: "Open Sans", Arial, sans-serif;
  }
  .card {
    position: absolute;
    left: 75px;
    top: 75px;
    width: 1050px;
    height: 597px;
    background: var(--card-black);
    border-radius: 36px;
    overflow: hidden;
    color: var(--white);
  }
  .brand {
    position: absolute;
    left: 55px;
    top: 145px;
    display: flex;
    align-items: center;
    gap: 18px;
  }
  .brand-dot {
    width: 58px;
    height: 58px;
    border-radius: 50%;
    background: var(--lime);
    flex: none;
  }
  .brand-name {
    margin: 0;
    font-size: 56px;
    font-weight: 700;
    line-height: 64px;
    color: var(--lime);
    letter-spacing: 0.5px;
    white-space: nowrap;
  }
  .services {
    position: absolute;
    left: 47px;
    top: 424px;
    margin: 0;
    padding: 0;
    list-style: none;
    font-size: 32px;
    line-height: 45px;
  }
  .services li {
    display: flex;
    align-items: center;
  }
  .services li::before {
    content: "";
    width: 9px;
    height: 9px;
    background: var(--white);
    margin-right: 13px;
  }
  .contact {
    position: absolute;
    left: 575px;
    top: 353px;
    height: 197px;
    padding-left: 24px;
    border-left: 1px solid var(--divider);
  }
  .person-name {
    margin: -6px 0 0;
    font-size: 30px;
    font-weight: 700;
    color: var(--lime);
    line-height: 36px;
  }
  .person-role {
    margin: 4px 0 8px;
    font-size: 24px;
    color: var(--lime);
    line-height: 32px;
  }
  .contact-line {
    display: flex;
    align-items: center;
    gap: 10px;
    margin: 0 0 0 -7px;
    font-size: 22px;
    line-height: 44px;
    white-space: nowrap;
  }
  .contact-line svg {
    width: 22px;
    height: 22px;
    flex: none;
  }
</style>
</head>
<body>
  <article class="card">
    <div class="brand">
      <span class="brand-dot"></span>
      <h1 class="brand-name">Bright Volley Tennis</h1>
    </div>

    <ul class="services">
      <li>Racquet Restringing</li>
      <li>Tennis Strings</li>
      <li>Accessories</li>
    </ul>

    <section class="contact">
      <h2 class="person-name">Owen Whitby</h2>
      <p class="person-role">Managing Director</p>
      <p class="contact-line">
        <svg viewBox="0 0 24 24" aria-hidden="true"><path fill="#b5d334" d="M2 9c0-3 4-5 10-5s10 2 10 5v2h-5V8.5c-1.5-.6-3.2-.9-5-.9s-3.5.3-5 .9V11H2zM6 12l3-3h6l3 3v7H6zm6 1.5a2.5 2.5 0 1 0 0 5 2.5 2.5 0 0 0 0-5z"/></svg>
        0491 726 305
      </p>
      <p class="contact-line">
        <svg viewBox="0 0 24 24" aria-hidden="true"><rect x="2" y="6" width="20" height="13" fill="none" stroke="#b5d334" stroke-width="2"/><path d="M2 6l10 7 10-7" fill="none" stroke="#b5d334" stroke-width="2"/></svg>
        brightvolleyracquets@mailbox.example
      </p>
      <p class="contact-line">
        <svg viewBox="0 0 24 24" aria-hidden="true"><circle cx="12" cy="12" r="9" fill="none" stroke="#b5d334" stroke-width="2"/><ellipse cx="12" cy="12" rx="4" ry="9" fill="none" stroke="#b5d334" stroke-width="1.6"/><path d="M3 12h18M5 7h14M5 17h14" stroke="#b5d334" stroke-width="1.4"/></svg>
        www.brightvolleyracquets.com.au
      </p>
    </section>
  </article>
</body>
</html>
```